Design 4 pages for an event discovery website

This is a contest for the design of 4 pages for an events discovery website. The feature is part of the new sign-up process.

Please see the attached document for a full scope, mockups and the parent category icons.

Target Market(s)

18-35 Australian event goers

Industry/Entity Type

Events

Number of Pages Required

4 page

```html
<!DOCTYPE html>
<html lang="en">
<head>
<meta charset="utf-8">
<title>Gigora – Signup</title>
<link rel="stylesheet" href="https://fonts.googleapis.com/css2?family=Open+Sans:wght@400;600&family=Ubuntu:wght@400;500;700&display=swap">
<style>
  :root {
    --brand-pink: #f5135f;
    --white: #ffffff;
    --panel-bg: rgba(10, 8, 20, 0.45);
    --panel-border: rgba(255, 255, 255, 0.35);
    --field-text: #555a60;
    --error-red: #e8141c;
    --ok-green: #8cc63f;
    --button-top: #ffd95a;
    --button-bottom: #ffc10e;
    --button-text: #6b4d06;
    --footer-bg: #1b1b1b;
    --footer-text: #bdbdbd;
  }
  * { box-sizing: border-box; margin: 0; padding: 0; }
  html, body { width: 1200px; height: 975px; overflow: hidden; }
  body {
    position: relative;
    font-family: "Open Sans", sans-serif;
    color: var(--white);
    background: var(--footer-bg);
  }

  /* Header */
  .site-header {
    position: absolute; left: 0; top: 0; width: 1200px; height: 92px;
    background: var(--brand-pink);
  }
  .brand {
    position: absolute; left: 60px; top: 24px;
    font-family: "Ubuntu", sans-serif; font-weight: 400; font-size: 35px;
    color: var(--white); letter-spacing: 0.5px;
  }
  .search {
    position: absolute; left: 750px; top: 25px; width: 217px; height: 44px;
    background: var(--white); border-radius: 22px;
    display: flex; align-items: center; padding-left: 17px; gap: 10px;
    font-size: 16px; color: #9a9a9a;
  }
  .auth-nav {
    position: absolute; right: 58px; top: 34px;
    font-family: "Ubuntu", sans-serif; font-size: 17px; color: var(--white);
    display: flex; gap: 16px;
  }

  /* Hero */
  .hero-backdrop {
    position: absolute; left: 0; top: 92px; width: 1200px; height: 778px;
    background:
      radial-gradient(ellipse 300px 200px at 1100px 60px, rgba(255,170,60,0.55), transparent 70%),
      radial-gradient(ellipse 260px 220px at 180px 60px, rgba(40,90,255,0.55), transparent 70%),
      radial-gradient(ellipse 420px 260px at 930px 560px, rgba(210,160,255,0.7), transparent 70%),
      radial-gradient(ellipse 380px 260px at 640px 460px, rgba(150,120,230,0.55), transparent 70%),
      radial-gradient(ellipse 300px 200px at 700px 250px, rgba(200,40,90,0.5), transparent 70%),
      linear-gradient(160deg, #1a2a8a 0%, #2a1450 35%, #120c24 60%, #3a1d5a 100%);
  }
  .panel {
    position: absolute; background: var(--panel-bg);
    border: 1px solid var(--panel-border);
  }
  .signup-panel { left: 60px; top: 157px; width: 425px; height: 669px; }
  .signup-title {
    position: absolute; left: 30px; top: 30px;
    font-family: "Ubuntu", sans-serif; font-size: 37px; font-weight: 400;
  }
  .field {
    position: absolute; left: 35px; width: 342px; height: 52px;
    background: var(--white); color: var(--field-text);
    font-size: 15.5px; display: flex; align-items: center;
    justify-content: space-between; padding: 2px 12px 0 17px;
  }
  .status { display: flex; align-items: center; gap: 8px; font-size: 17px; }
  .status--taken { color: var(--error-red); }
  .status--free { color: var(--ok-green); }
  .signup-button {
    position: absolute; left: 35px; top: 547px; width: 344px; height: 69px;
    border: none; border-radius: 3px;
    background: linear-gradient(var(--button-top), var(--button-bottom));
    font-family: "Ubuntu", sans-serif; font-weight: 700; font-size: 34px;
    color: var(--button-text); letter-spacing: 0.5px;
  }

  .benefits-panel { left: 503px; top: 157px; width: 638px; height: 271px; }
  .benefit-list { list-style: none; position: absolute; left: 24px; top: 44px; }
  .benefit-list li {
    display: flex; align-items: center; height: 33.3px;
    font-size: 15.5px;
  }
  .benefit-list svg { margin-right: 14px; flex: none; }

  /* Footer */
  .site-footer {
    position: absolute; left: 0; top: 870px; width: 1200px; height: 105px;
    background: var(--footer-bg); color: var(--footer-text);
  }
  .footer-nav {
    position: absolute; left: 60px; top: 29px; font-size: 14px;
    display: flex; gap: 16px;
  }
  .copyright { position: absolute; left: 60px; top: 60px; font-size: 14px; }
  .social {
    position: absolute; top: 29px; width: 46px; height: 46px;
    border: 1px solid var(--footer-text); border-radius: 50%;
  }
</style>
</head>
<body>
  <header class="site-header">
    <div class="brand">Gigora</div>
    <div class="search">
      <svg width="14" height="14" viewBox="0 0 14 14" aria-hidden="true">
        <circle cx="5.5" cy="5.5" r="4.2" fill="none" stroke="#555" stroke-width="2"/>
        <line x1="8.6" y1="8.6" x2="12.8" y2="12.8" stroke="#555" stroke-width="2.2" stroke-linecap="round"/>
      </svg>
      Search
    </div>
    <nav class="auth-nav"><span>Sign up</span><span>|</span><span>Login</span></nav>
  </header>

  <div class="hero-backdrop" role="img" aria-label="Blurred concert photo of a drum kit under stage lights"></div>

  <section class="panel signup-panel">
    <h1 class="signup-title">Signup</h1>
    <div class="field" style="top:101px">Username
      <span class="status status--taken">
        <svg width="12" height="12" viewBox="0 0 12 12" aria-hidden="true"><path d="M1.5 1.5l9 9M10.5 1.5l-9 9" stroke="currentColor" stroke-width="3" stroke-linecap="round"/></svg>
        Not Available</span>
    </div>
    <div class="field" style="top:166px">Email Address
      <span class="status status--free">
        <svg width="16" height="13" viewBox="0 0 16 13" aria-hidden="true"><path d="M1.5 7l4.5 4.5L14.5 2" fill="none" stroke="currentColor" stroke-width="3"/></svg>
        Available</span>
    </div>
    <div class="field" style="top:229px">Password</div>
    <div class="field" style="top:290px">Confirm Password</div>
    <div class="field" style="top:353px">First name</div>
    <div class="field" style="top:415px">Last name</div>
    <div class="field" style="top:478px">Date of Birth</div>
    <button class="signup-button">SIGN UP</button>
  </section>

  <section class="panel benefits-panel">
    <ul class="benefit-list">
      <li><svg width="22" height="20" viewBox="0 0 22 20" aria-hidden="true"><rect x="1.5" y="3.5" width="15" height="15" rx="2" fill="none" stroke="#fff" stroke-width="2.4"/><path d="M5 10l4 4 11-12" fill="none" stroke="#fff" stroke-width="3"/></svg>Get personalised event recommendations</li>
      <li><svg width="22" height="20" viewBox="0 0 22 20" aria-hidden="true"><rect x="1.5" y="3.5" width="15" height="15" rx="2" fill="none" stroke="#fff" stroke-width="2.4"/><path d="M5 10l4 4 11-12" fill="none" stroke="#fff" stroke-width="3"/></svg>Get notified about your favourite events - never miss out again</li>
      <li><svg width="22" height="20" viewBox="0 0 22 20" aria-hidden="true"><rect x="1.5" y="3.5" width="15" height="15" rx="2" fill="none" stroke="#fff" stroke-width="2.4"/><path d="M5 10l4 4 11-12" fill="none" stroke="#fff" stroke-width="3"/></svg>Follow all your favourite artists, musicians, teams and players in one place</li>
      <li><svg width="22" height="20" viewBox="0 0 22 20" aria-hidden="true"><rect x="1.5" y="3.5" width="15" height="15" rx="2" fill="none" stroke="#fff" stroke-width="2.4"/><path d="M5 10l4 4 11-12" fill="none" stroke="#fff" stroke-width="3"/></svg>Follow your favourite local venues to know everything happening there</li>
      <li><svg width="22" height="20" viewBox="0 0 22 20" aria-hidden="true"><rect x="1.5" y="3.5" width="15" height="15" rx="2" fill="none" stroke="#fff" stroke-width="2.4"/><path d="M5 10l4 4 11-12" fill="none" stroke="#fff" stroke-width="3"/></svg>Get curated news and feature content on your favourite artists (coming soon)</li>
      <li><svg width="22" height="20" viewBox="0 0 22 20" aria-hidden="true"><rect x="1.5" y="3.5" width="15" height="15" rx="2" fill="none" stroke="#fff" stroke-width="2.4"/><path d="M5 10l4 4 11-12" fill="none" stroke="#fff" stroke-width="3"/></svg>Invite your mates to events via Linkverse (LV sign-up only)</li>
    </ul>
  </section>

  <footer class="site-footer">
    <nav class="footer-nav">
      <span>Home</span><span>|</span><span>Events</span><span>|</span><span>Artists</span><span>|</span><span>Location</span><span>|</span><span>Blog</span><span>|</span><span>Contact</span>
    </nav>
    <p class="copyright">© 2015 All Rights Reserved.</p>
    <span class="social" style="left:969px"></span>
    <span class="social" style="left:1032px"></span>
    <span class="social" style="left:1094px"></span>
  </footer>
</body>
</html>
```